Brisk Hound Signage

This design is for "signage" that we intend to get produced.
A couple of different designs that say "Brisk Hound on Guard" and "Beware of Brisk Hound"
It should also have our logo (BH) plus our logo with the hand and dog paw. We would also like the main picture of the sign to be the attached. We would like a classy sophisticated look similar to our logo you designed.
Our designs will go on consumers gates/entrances to warn people there is a dog on the premises. I will get a better quality picture of the dog.

```html
<!DOCTYPE html>
<html lang="en">
<head>
<meta charset="utf-8">
<title>Brisk Hound Signage</title>
<link rel="stylesheet" href="https://fonts.googleapis.com/css2?family=Jost:wght@400;500&family=Pinyon+Script&display=swap">
<style>
  :root {
    --backdrop: #e4e4e4;
    --sign-face: #ffffff;
    --ring: #9dabe0;
    --brand: #8e9dd8;
    --ink: #1c1c1c;
    --dog-dark: #3a3a3a;
    --dog-mid: #5a5a5a;
    --shadow-soft: rgba(0, 0, 0, 0.12);
  }
  * { box-sizing: border-box; margin: 0; padding: 0; }
  html, body {
    width: 1200px;
    height: 2879px;
    overflow: hidden;
    background: var(--backdrop);
  }
  .signage-sheet {
    width: 1200px;
    height: 2879px;
    display: flex;
    flex-direction: column;
    align-items: center;
    justify-content: center;
    gap: 300px;
  }
  .sign {
    position: relative;
    width: 960px;
    height: 960px;
    border-radius: 50%;
    background: var(--sign-face);
    box-shadow: 0 6px 24px var(--shadow-soft);
  }
  .sign__ring {
    position: absolute;
    inset: 40px;
    border-radius: 50%;
    border: 6px solid var(--ring);
  }
  .sign__brand {
    position: absolute;
    top: 185px;
    left: 0;
    right: 0;
    display: flex;
    align-items: center;
    justify-content: center;
    gap: 22px;
  }
  .brand__dot {
    width: 96px;
    height: 96px;
    border-radius: 50%;
    border: 4px solid var(--brand);
  }
  .brand__name {
    font-family: "Jost", sans-serif;
    font-weight: 400;
    font-size: 44px;
    letter-spacing: 4px;
    text-transform: uppercase;
    color: var(--brand);
  }
  .sign__kicker {
    position: absolute;
    left: 0;
    right: 0;
    text-align: center;
    font-family: "Jost", sans-serif;
    font-weight: 500;
    color: var(--ink);
    letter-spacing: 3px;
    text-transform: uppercase;
  }
  .sign__name {
    position: absolute;
    left: 0;
    right: 0;
    text-align: center;
    font-family: "Pinyon Script", cursive;
    font-weight: 400;
    font-size: 150px;
    line-height: 1;
    color: var(--ink);
  }
  .sign--beware .sign__kicker { top: 320px; font-size: 70px; }
  .sign--beware .sign__name { top: 410px; }
  .sign--guard .sign__name { top: 330px; }
  .sign--guard .sign__kicker { top: 500px; font-size: 74px; }
  .sign__dog {
    position: absolute;
    left: 50%;
    top: 590px;
    width: 300px;
    height: 290px;
    transform: translateX(-50%);
    border-radius: 40% 40% 12% 12%;
    background: radial-gradient(ellipse at 50% 40%, var(--dog-mid), var(--dog-dark) 70%);
  }
  .sign--guard .sign__dog { top: 600px; }
</style>
</head>
<body>
  <main class="signage-sheet">
    <section class="sign sign--beware" aria-label="Beware of Brisk Hound sign">
      <div class="sign__ring"></div>
      <div class="sign__brand">
        <span class="brand__dot"></span>
        <span class="brand__name">Brisk Hound</span>
      </div>
      <p class="sign__kicker">Beware of</p>
      <p class="sign__name">Brisk Hound</p>
      <div class="sign__dog" role="img" aria-label="Dark faceted sculpture of a seated dog with a soft shadow beneath"></div>
    </section>

    <section class="sign sign--guard" aria-label="Brisk Hound on Guard sign">
      <div class="sign__ring"></div>
      <div class="sign__brand">
        <span class="brand__dot"></span>
        <span class="brand__name">Brisk Hound</span>
      </div>
      <p class="sign__name">Brisk Hound</p>
      <p class="sign__kicker">On Guard</p>
      <div class="sign__dog" role="img" aria-label="Dark faceted sculpture of a seated dog with a soft shadow beneath"></div>
    </section>
  </main>
</body>
</html>
```